Poem Design for Storytelling Company

Who Are We?
Venra Studio is a storytelling company that focuses on producing artistic content and delivering immersive experiences to inspire us in discovering our inner utopia.
What is Inner Utopia?
We believe an inner utopia exists within every one of us. It is a state of being where one truly accepts and appreciates the holistic and dualistic nature of the self, others and life as a whole. It is the true acceptance of self, true connections with others, full accountability and ownership of one’s problems and true appreciation of life.
Art Direction:
Negative Space Design is the central theme & focal point of our designs. It is deeply ingrained & firmly rooted in Venra’s ethos of Discover Your Inner Utopia. It is both simple & complex. It represents the journey of self-discovery & actualisation: a deeply personal experience. Negative Space is black & white, two extremes, polar opposites, the Yin and Yang. Yet despite the two opposing contrasts, lies the ultimate reality which is the very heart & soul of Negative Space: Perspective. It is neither wrong nor right nor is it black or white. It is everything, yet nothing.
Deliverable:
We are looking for a designer to create art pieces that will supplement our original poems. We are looking to post these poems on Instagram, we and we aim to give our readers an immersive and emotional experience while reading these poems. Since our poems are fairly long, we anticipate the use of a couple of images for each poems (i.e Each image will cover a coupe of lines).
Please refer below to our poems:
1. Where Does It Go?
Where Does It Go?
This is what they told me
To Win, and Not to Lose
To Succeed, and Not to Fail
To Laugh, and Not to Cry
To Fear, and Not to Try
To Be, or Not to Be
For Me, or Not for Me?
Trying to do what I am supposed to do
Hoping to be who I am supposed to be
Fearing to do what I wanted to do
Trapped in my body, I want to be free
Until One Day, I am on My Deathbed
Reflecting and thinking about what I regret
Realizing it was about nothing they said
It was me, who didn’t live the life that I had
For those who still have the chance
Smell the roses, and enjoy the dance
2. Ember (Please see uploaded files)
Design References:
https://files.plunkbox.example/share/8XqLt2VwRm4Hs7PjKd9Ne3Bc6YfGzA1Uo?mode=view

```html
<!DOCTYPE html>
<html lang="en">
<head>
<meta charset="utf-8">
<title>Where Does It Go? — Venra Studio</title>
<link href="https://fonts.googleapis.com/css2?family=Kalam:wght@400&display=swap" rel="stylesheet">
<style>
  :root {
    --sky-light: #e6f5fb;
    --sky-mid: #a9dcf0;
    --sky-deep: #7fcbe9;
    --band-blue: #00b2ee;
    --paper: #ffffff;
    --paper-shade: #e9e9e9;
    --ink: #111111;
    --vine-pink: #d92a93;
  }
  * { box-sizing: border-box; margin: 0; padding: 0; }
  html, body { width: 1200px; height: 1200px; overflow: hidden; background: var(--sky-light); }
  .poem-card {
    position: relative;
    width: 1200px;
    height: 1200px;
    overflow: hidden;
  }
  .watercolor-field {
    position: absolute;
    inset: 0;
    background:
      radial-gradient(ellipse 300px 420px at 60px 700px, rgba(217,42,147,0.35), transparent 70%),
      radial-gradient(ellipse 220px 380px at 1120px 420px, rgba(217,42,147,0.28), transparent 70%),
      radial-gradient(ellipse 520px 380px at 420px 260px, rgba(255,255,255,0.75), transparent 70%),
      radial-gradient(ellipse 600px 500px at 800px 900px, rgba(127,203,233,0.6), transparent 70%),
      linear-gradient(160deg, var(--sky-mid), var(--sky-light) 45%, var(--sky-deep) 100%);
  }
  .line-band {
    position: absolute;
    background: var(--band-blue);
  }
  .paper-strip {
    position: absolute;
    display: flex;
    align-items: center;
    background: linear-gradient(180deg, var(--paper) 0%, var(--paper) 70%, var(--paper-shade) 100%);
    box-shadow: 0 4px 8px rgba(0,0,0,0.25);
    clip-path: polygon(0% 6%, 4% 3%, 9% 6%, 15% 2%, 22% 5%, 30% 2%, 38% 6%, 46% 3%, 55% 5%, 63% 2%, 71% 6%, 80% 3%, 88% 5%, 95% 2%, 100% 4%,
                       100% 95%, 94% 98%, 87% 94%, 80% 97%, 72% 93%, 64% 97%, 56% 94%, 48% 98%, 40% 94%, 32% 97%, 24% 93%, 16% 97%, 8% 94%, 3% 98%, 0% 95%);
  }
  .poem-line {
    font-family: 'Kalam', cursive;
    font-weight: 400;
    color: var(--ink);
    font-size: 44px;
    line-height: 1;
    white-space: nowrap;
    padding-top: 8px;
  }
  .band-win { left: 402px; top: 261px; width: 744px; height: 136px; }
  .strip-win { left: 537px; top: 245px; width: 572px; height: 118px; padding-left: 26px; transform: rotate(-0.4deg); }

  .band-succeed { left: 102px; top: 491px; width: 743px; height: 115px; }
  .strip-succeed { left: 90px; top: 432px; width: 674px; height: 150px; padding-left: 46px; transform: rotate(2.8deg); }

  .band-laugh { left: 481px; top: 779px; width: 730px; height: 66px; }
  .strip-laugh { left: 463px; top: 680px; width: 750px; height: 110px; padding-left: 36px; transform: rotate(-0.6deg); }

  .band-fear { left: 283px; top: 956px; width: 562px; height: 119px; }
  .strip-fear { left: 360px; top: 907px; width: 522px; height: 130px; padding-left: 28px; transform: rotate(-1deg); }
</style>
</head>
<body>
  <main class="poem-card">
    <div class="watercolor-field" role="img" aria-label="Blue and white watercolour background with magenta leafy vines climbing along the edges"></div>

    <div class="line-band band-win"></div>
    <div class="paper-strip strip-win"><p class="poem-line">To Win, and Not to Lose</p></div>

    <div class="line-band band-succeed"></div>
    <div class="paper-strip strip-succeed"><p class="poem-line">To Succeed, and Not to Fail</p></div>

    <div class="line-band band-laugh"></div>
    <div class="paper-strip strip-laugh"><p class="poem-line">To Laugh, and Not to Cry</p></div>

    <div class="line-band band-fear"></div>
    <div class="paper-strip strip-fear"><p class="poem-line">To Fear, and Not to Try</p></div>
  </main>
</body>
</html>
```